Federal IT Consulting Company - Brisolux Consulting Group

We're seeking a skilled web designer to create a modern, bold, and engaging WordPress website for Brisolux Consulting Group, LLC. Our company specializes in federal IT consulting, and our name is a play on "Brightening Solutions." The website should reflect our expertise in the federal technology marketplace and position us as a trusted partner for clients navigating their IT journey.

contact: info@brisoluxgrp-example.com

Current Status

WordPress is already installed on our hosting account
We have an existing logo (may need modernization)

Design Requirements

Style:

Modern and visually striking design
Bold elements to convey confidence and expertise
Incorporate the concept of "brightening solutions" into the design

Features:

Modern UX sliders for dynamic content presentation
Eye-catching, high-quality images (stock photos to be sourced by the designer)
Responsive design for all devices

Color Scheme:

To be proposed by the designer, should align with our brand and convey trust and technological expertise

Logo:

Evaluate our current logo
Create a transparent background version if needed
Propose modernization if deemed necessary

Accessibility:

Ensure design elements are accessible to users with disabilities
Use high contrast ratios for text and background colors
Provide text alternatives for non-text content

Website Structure
Create the following pages, with the possibility of subpages:

Home
Services
About
Contact

Specific Page Requirements
Home Page

Striking hero section with a clear value proposition
Overview of our services
Client testimonials or trust indicators

Services Page

Detailed list of our IT consulting services
Clear explanation of how we help navigate the federal IT landscape

About Page

Company history and mission
Team highlights (if applicable)
Our approach to federal IT consulting

Contact Page

Contact form
Other contact methods (phone, email)

Technical Requirements

Fully responsive design
SEO best practices implemented
Fast loading times
Integration with necessary plugins (to be discussed)
Training on how to update and maintain the site
Full compliance with Web Content Accessibility Guidelines (WCAG) 2.1 Level AA
Adherence to Section 508 standards for federal website accessibility
Implementation of necessary features for ADA compliance
Updates

Designs look the same

Target Market(s)

US Federal Govt customers looking for IT support.

Industry/Entity Type

IT Consulting

Coding

Coded - Design and coding required

Colors
0054AA
0677BA
7BADD7
CADEEF
E8F1F8
0094D4
00A9DD
6FCCEA
C7EBF8
E9F6FB
00AB8E
00BBA5
67D7C9
C6EFE9
E9F9F6

```html
<!DOCTYPE html>
<html lang="en">
<head>
<meta charset="utf-8">
<title>Brisolux Federal Services</title>
<link rel="stylesheet" href="https://fonts.googleapis.com/css2?family=Lexend:wght@400;500;600&family=Urbanist:wght@400;500;600;700&family=Montserrat:wght@400;500;600&display=swap">
<style>
:root{
  --blue-deep:#0054AA;
  --blue:#0677BA;
  --sky:#0094D4;
  --sky-light:#7BADD7;
  --ice:#E8F1F8;
  --ink:#2b2b2b;
  --text:#222;
  --muted:#555;
  --grey-bg:#f0f0f0;
  --navy:#14204f;
  --white:#fff;
}
*{margin:0;padding:0;box-sizing:border-box}
html,body{width:1200px;height:3701px;overflow:hidden}
body{position:relative;background:var(--white);font-family:"Montserrat",sans-serif;color:var(--text)}
.abs{position:absolute}
.heading{font-family:"Lexend",sans-serif;font-weight:500;color:var(--ink);letter-spacing:-.5px;text-transform:uppercase}
.label{font-family:"Lexend",sans-serif;font-weight:400;color:var(--blue);text-transform:uppercase;font-size:20px}
.underline{height:3px;width:50px;background:var(--blue)}
.centered{left:0;width:1200px;text-align:center}

/* header */
.site-header{top:0;left:0;width:1200px;height:70px;background:var(--white)}
.brand{left:141px;top:16px;display:flex;align-items:center;gap:10px;font-family:"Urbanist",sans-serif;font-weight:700;font-size:30px;color:var(--blue-deep);letter-spacing:1px}
.brand .dot{width:26px;height:26px;border-radius:50%;background:var(--sky)}
.nav{top:27px;font-family:"Urbanist",sans-serif;font-weight:600;font-size:15px;color:#111}
.nav.active{color:var(--sky)}
.nav-cta{left:950px;top:14px;width:108px;height:42px;border-radius:4px;background:var(--sky);color:#fff;font-family:"Urbanist",sans-serif;font-weight:600;font-size:15px;display:flex;align-items:center;justify-content:center;box-shadow:0 3px 8px rgba(0,148,212,.35)}

/* hero */
.hero{top:70px;left:0;width:1200px;height:487px;background:linear-gradient(90deg,#1c2530 0%,#3a4450 38%,#7b7670 62%,#a99f96 100%)}
.hero-kicker{left:141px;top:170px;padding-left:10px;border-left:2px solid #fff;font-family:"Urbanist",sans-serif;font-size:13px;font-weight:500;color:#fff;letter-spacing:.5px}
.hero-title{left:141px;top:197px;font-family:"Urbanist",sans-serif;font-weight:700;font-size:37px;line-height:46px;color:#fff}
.hero-sub{left:141px;top:358px;font-family:"Urbanist",sans-serif;font-size:15px;line-height:25px;color:#fff}
.btn{display:flex;align-items:center;justify-content:center;font-family:"Urbanist",sans-serif;font-weight:600;font-size:14px;color:#fff;border-radius:4px}
.btn-solid{left:141px;top:434px;width:171px;height:42px;background:var(--sky)}
.btn-ghost{left:326px;top:434px;width:190px;height:42px;border:1.5px solid #fff}

/* about */
.about-arch{left:147px;top:652px;width:206px;height:383px;border-radius:103px 0 103px 0;background:linear-gradient(180deg,#3f7fd0 0%,#8fb6e2 45%,#d9dde2 100%)}
.about-arch2{left:365px;top:757px;width:249px;height:341px;border-radius:0 125px 0 0;background:linear-gradient(180deg,#c9cfd6 0%,#8b9198 50%,#3b4350 100%)}
.badge-num{left:369px;top:652px;width:72px;height:74px;background:var(--blue-deep);border-radius:20px 0 0 0;color:#fff;font-family:"Lexend",sans-serif;font-weight:600;font-size:26px;display:flex;align-items:center;justify-content:center}
.badge-text{left:450px;top:652px;width:164px;height:74px;border:1px solid #ccc;border-radius:0 0 30px 0;padding:14px 18px;font-family:"Urbanist",sans-serif;font-size:18px;line-height:22px;color:#222}
.about-label{left:671px;top:684px}
.about-title{left:671px;top:706px;font-size:37px}
.about-line{left:671px;top:752px;width:70px}
.about-copy{left:671px;top:776px;width:390px;font-family:"Urbanist",sans-serif;font-size:13px;line-height:21.6px;letter-spacing:.6px;color:#222;text-align:justify}
.about-copy p+p{margin-top:6px}
.about-copy strong{font-weight:600}
.btn-pill{left:671px;top:1025px;width:129px;height:44px;border-radius:22px;background:var(--blue-deep);font-family:"Lexend",sans-serif;font-size:13px}
.edge-mark{left:1172px;top:700px;width:28px;height:26px;border-right:1.5px solid #333;border-bottom:1.5px solid #333}

/* services */
.services-photo{left:0;top:1183px;width:340px;height:523px;background:linear-gradient(180deg,#b8c1cb 0%,#6b7480 55%,#2e3440 100%)}
.services-panel{left:141px;top:1183px;width:1059px;height:523px;background:var(--blue-deep);border-radius:210px 0 0 0}
.services-label{left:282px;top:1262px;color:#fff}
.services-title{left:282px;top:1284px;font-size:37px;color:#fff}
.services-line{left:282px;top:1329px;width:70px;background:#fff}
.services-intro{left:672px;top:1272px;width:400px;font-size:13px;line-height:22px;color:#fff}
.card{top:1362px;width:240px;height:237px;background:#fff;border-radius:0 75px 0 0}
.card .icon{position:absolute;left:32px;top:25px;width:65px;height:65px;border-radius:50%;background:var(--blue-deep);display:flex;align-items:center;justify-content:center}
.card h3{position:absolute;left:32px;top:105px;font-family:"Lexend",sans-serif;font-weight:500;font-size:15px;color:#222}
.card p{position:absolute;left:32px;top:135px;width:185px;font-size:12.5px;line-height:21.5px;color:#333}
.round-arrow{width:38px;height:38px;border-radius:50%;background:#fff;border:1px solid #ddd;display:flex;align-items:center;justify-content:center}

/* testimonials */
.t-intro{top:1874px;left:170px;width:860px;text-align:center;font-size:13px;line-height:22px;color:#222}
.t-card{top:1966px;width:423px;height:230px;border:1px solid #ccc;background:#fff}
.t-photo{top:1940px;width:114px;height:131px;background:linear-gradient(180deg,#9aa3ad,#3c434d)}
.t-name{top:2003px;font-family:"Lexend",sans-serif;font-weight:500;font-size:18px;color:#222}
.t-role{top:2030px;font-size:11px;color:#444}
.t-stars{top:2048px;font-size:15px;color:#f5b301;letter-spacing:3px}
.t-quote{top:1967px;width:46px;height:66px;background:var(--blue-deep);clip-path:polygon(0 0,100% 0,100% 100%,50% 82%,0 100%)}
.t-body{top:2094px;width:330px;font-size:12.5px;line-height:21px;color:#333}
.nav-arrow{width:30px;height:30px;border-radius:50%;display:flex;align-items:center;justify-content:center}
.nav-arrow.light{background:#fff;border:1px solid #ccc}
.nav-arrow.dark{background:var(--sky)}

/* team */
.team-bg{left:0;top:2282px;width:1200px;height:631px;background:var(--grey-bg)}
.team-frame{top:2533px;width:234px;height:227px;border:1px solid #ddd;background:#f4f4f4}
.team-photo{top:2462px;width:205px;height:288px}
.team-notch{top:2752px;width:16px;height:16px;background:#f4f4f4;border-right:1px solid #ddd;border-bottom:1px solid #ddd;transform:rotate(45deg)}
.team-name{top:2786px;width:260px;text-align:center;font-family:"Lexend",sans-serif;font-weight:500;font-size:18px;color:#333}
.team-role{top:2816px;width:260px;text-align:center;font-size:11.5px;letter-spacing:3px;color:var(--blue);font-weight:500}

/* certifications */
.cert{top:3094px;width:168px;height:112px}

/* footer */
.footer{left:0;top:3322px;width:1200px;height:338px;background:var(--navy)}
.f-head{top:3380px;font-family:"Lexend",sans-serif;font-weight:600;font-size:17px;color:#fff}
.f-line{top:3410px;width:32px;height:2px;background:#fff}
.f-link{font-size:12.5px;color:#fff}
.f-sub{font-weight:600}
.f-icon{display:inline-block;width:10px;height:10px;border-radius:50%;background:#fff;margin-right:10px;vertical-align:middle}
.copyright{left:0;top:3660px;width:1200px;height:41px;background:var(--blue);color:#fff;font-size:12.5px;display:flex;align-items:center;justify-content:center}
</style>
</head>
<body>

<header class="abs site-header">
  <div class="abs brand"><span class="dot"></span>BRISOLUX</div>
  <nav>
    <span class="abs nav active" style="left:695px">Home</span>
    <span class="abs nav" style="left:769px">About Us</span>
    <span class="abs nav" style="left:862px">Services</span>
    <span class="abs nav-cta">Contact Us</span>
  </nav>
</header>

<section class="abs hero" role="img" aria-label="Two consultants reviewing a tablet together in a bright office"></section>
<div class="abs hero-kicker">WELCOME TO BRISOLUX</div>
<h1 class="abs hero-title">Navigate Your Federal<br>IT Journey with<br>Confidence.</h1>
<p class="abs hero-sub">Expert Consulting Services to Guide Your<br>IT Strategy.</p>
<span class="abs btn btn-solid">Explore Our Services</span>
<span class="abs btn btn-ghost">Get A Free Consultation</span>

<div class="abs about-arch" role="img" aria-label="Government building under a blue sky with a flag"></div>
<div class="abs about-arch2" role="img" aria-label="Consultant reviewing documents at a desk with flags"></div>
<div class="abs badge-num">15+</div>
<div class="abs badge-text">Year of<br>Experience</div>
<div class="abs label about-label">About</div>
<h2 class="abs heading about-title">Calmed Forces</h2>
<div class="abs underline about-line"></div>
<div class="abs about-copy">
  <p><strong>Lorem Ipsum is simply dummy text of the printing and typesetting industry. Lorem Ipsum has been the industry's standard dummy text ever since</strong></p>
  <p>Lorem Ipsum is simply dummy text of the printing and typesetting industry. Lorem Ipsum has been the industry's standard dummy text ever since the 1500s, when an unknown printer took a galley of type and scrambled it to make a type specimen book. It has survived not only five centuries, but also the leap into electronic typesetting, remaining essentially unchanged. It was popularised in the 1960s with the release of Letraset sheets containing</p>
</div>
<span class="abs btn btn-pill">READ MORE</span>
<div class="abs edge-mark"></div>

<div class="abs services-photo" role="img" aria-label="Business professionals in suits walking together"></div>
<section class="abs services-panel"></section>
<div class="abs label services-label">Practice Areas</div>
<h2 class="abs heading services-title">Our Services</h2>
<div class="abs underline services-line"></div>
<p class="abs services-intro">Lorem Ipsum is simply dummy text of the printing and amet sit typesetting industry.</p>

<article class="abs card" style="left:283px">
  <div class="icon"><svg width="30" height="34" viewBox="0 0 30 34" fill="none" stroke="#fff" stroke-width="2"><path d="M15 2 L27 7 V16 C27 24 21 30 15 32 C9 30 3 24 3 16 V7 Z"/><rect x="10" y="15" width="10" height="9" rx="1"/><path d="M12 15 V12 a3 3 0 0 1 6 0"/></svg></div>
  <h3>Cybersecurity</h3>
  <p>Duis aute irure dolor in amet reprehenderit in voluptate ut velit esse cillum dolore.</p>
</article>
<article class="abs card" style="left:550px">
  <div class="icon"><svg width="34" height="32" viewBox="0 0 34 32" fill="none" stroke="#fff" stroke-width="2"><path d="M9 18 a6 6 0 0 1 1-12 a8 8 0 0 1 15 2 a5 5 0 0 1 0 10 Z"/><path d="M12 18 v6 M17 18 v9 M22 18 v6"/><circle cx="12" cy="26" r="1.5"/><circle cx="17" cy="29" r="1.5"/><circle cx="22" cy="26" r="1.5"/></svg></div>
  <h3>Cloud Services</h3>
  <p>Duis aute irure dolor in amet reprehenderit in voluptate ut velit esse cillum dolore.</p>
</article>
<article class="abs card" style="left:818px">
  <div class="icon"><svg width="34" height="32" viewBox="0 0 34 32" fill="none" stroke="#fff" stroke-width="2"><rect x="12" y="3" width="19" height="13" rx="1"/><circle cx="7" cy="10" r="3"/><path d="M2 28 V19 a5 5 0 0 1 10 0 V28"/><path d="M12 20 L20 14"/><path d="M16 8 h10 M16 12 h7"/></svg></div>
  <h3>It Strategy Consulting</h3>
  <p>Duis aute irure dolor in amet reprehenderit in voluptate ut velit esse cillum dolore.</p>
</article>
<div class="abs round-arrow" style="left:385px;top:1580px"><svg width="14" height="10" viewBox="0 0 14 10" fill="none" stroke="#0054AA" stroke-width="1.5"><path d="M1 5 H12 M8 1 L12 5 L8 9"/></svg></div>
<div class="abs round-arrow" style="left:652px;top:1584px"><svg width="14" height="10" viewBox="0 0 14 10" fill="none" stroke="#0054AA" stroke-width="1.5"><path d="M1 5 H12 M8 1 L12 5 L8 9"/></svg></div>
<div class="abs round-arrow" style="left:919px;top:1580px"><svg width="14" height="10" viewBox="0 0 14 10" fill="none" stroke="#0054AA" stroke-width="1.5"><path d="M1 5 H12 M8 1 L12 5 L8 9"/></svg></div>

<div class="abs label centered" style="top:1784px">Testimonials</div>
<h2 class="abs heading centered" style="top:1806px;font-size:37px">What Our Customers Say</h2>
<p class="abs t-intro">Duis aute irure dolor in reprehenderit in voluptate velit esse cillum dolore eu fugiat nulla pariatur. Excepteur sint occaecat cupidatat non proident, sunt in culpa qui officia deserunt mollit anim id est laborum.</p>

<div class="abs t-card" style="left:161px"></div>
<div class="abs t-photo" style="left:142px" role="img" aria-label="Portrait of a client in a dark suit"></div>
<div class="abs t-name" style="left:272px">Dale Morrow</div>
<div class="abs t-role" style="left:272px">Lorem Ipsum</div>
<div class="abs t-stars" style="left:272px">★★★★★</div>
<div class="abs t-quote" style="left:502px"></div>
<svg class="abs" style="left:511px;top:1985px" width="28" height="22" viewBox="0 0 28 22" fill="#fff"><path d="M2 0 h10 v10 l-5 12 h-5 l4-12 h-4z M16 0 h10 v10 l-5 12 h-5 l4-12 h-4z"/></svg>
<p class="abs t-body" style="left:201px">Lorem ipsum dolor sit amet, consectetur adipiscing elit, sed do eiusmod tempor incididunt ut labore et dolore magna aliqua. Ut enim ad minim veniam, quis nostrud exercitation ullamco.</p>

<div class="abs t-card" style="left:635px"></div>
<div class="abs t-photo" style="left:615px" role="img" aria-label="Portrait of a client in a dark blazer"></div>
<div class="abs t-name" style="left:746px">Renata Solis</div>
<div class="abs t-role" style="left:746px">Lorem Ipsum</div>
<div class="abs t-stars" style="left:746px">★★★★★</div>
<div class="abs t-quote" style="left:976px"></div>
<svg class="abs" style="left:985px;top:1985px" width="28" height="22" viewBox="0 0 28 22" fill="#fff"><path d="M2 0 h10 v10 l-5 12 h-5 l4-12 h-4z M16 0 h10 v10 l-5 12 h-5 l4-12 h-4z"/></svg>
<p class="abs t-body" style="left:675px">Lorem ipsum dolor sit amet, consectetur adipiscing elit, sed do eiusmod tempor incididunt ut labore et dolore magna aliqua. Ut enim ad minim veniam, quis nostrud exercitation ullamco.</p>

<div class="abs nav-arrow light" style="left:93px;top:2066px"><svg width="12" height="10" viewBox="0 0 12 10" fill="#111"><path d="M0 5 L5 1 V4 H12 V6 H5 V9 Z"/></svg></div>
<div class="abs nav-arrow dark" style="left:1076px;top:2066px"><svg width="12" height="10" viewBox="0 0 12 10" fill="#fff"><path d="M12 5 L7 1 V4 H0 V6 H7 V9 Z"/></svg></div>

<section class="abs team-bg"></section>
<div class="abs label centered" style="top:2362px">Staff</div>
<h2 class="abs heading centered" style="top:2384px;font-size:37px">Our Team Members</h2>
<div class="abs underline" style="left:565px;top:2430px;width:70px"></div>

<div class="abs team-frame" style="left:221px"></div>
<div class="abs team-notch" style="left:330px"></div>
<div class="abs team-photo" style="left:236px;background:linear-gradient(180deg,#7fb3b3,#4e7f80)" role="img" aria-label="Portrait of a team member in a burgundy blazer"></div>
<div class="abs team-name" style="left:208px">Nora Whitfield</div>
<div class="abs team-role" style="left:208px">ADVICER</div>

<div class="abs team-frame" style="left:483px"></div>
<div class="abs team-notch" style="left:592px"></div>
<div class="abs team-photo" style="left:498px;background:linear-gradient(180deg,#3d5a80,#b7a38a)" role="img" aria-label="Portrait of a team member in a tan suit"></div>
<div class="abs team-name" style="left:470px">Owen Hartley</div>
<div class="abs team-role" style="left:470px">MANAGER</div>

<div class="abs team-frame" style="left:745px"></div>
<div class="abs team-notch" style="left:853px"></div>
<div class="abs team-photo" style="left:760px;background:linear-gradient(180deg,#9aa1a8,#e6e8ea)" role="img" aria-label="Portrait of a team member in a white shirt"></div>
<div class="abs team-name" style="left:732px">Elliot Crane</div>
<div class="abs team-role" style="left:732px">FOUNDER</div>

<div class="abs label centered" style="top:2993px">Expertise</div>
<h2 class="abs heading centered" style="top:3015px;font-size:37px">Our Certifications</h2>
<div class="abs cert" style="left:142px;background:linear-gradient(135deg,#b3121b,#e9c96b 50%,#b3121b)" role="img" aria-label="Certificate of appreciation"></div>
<div class="abs cert" style="left:329px;background:linear-gradient(135deg,#f4a21d,#fdf6ea 55%,#f3801f)" role="img" aria-label="Certificate of achievement"></div>
<div class="abs cert" style="left:516px;background:linear-gradient(135deg,#c9283a,#f7f4f1 45%,#2b4c3f)" role="img" aria-label="Certificate of appreciation"></div>
<div class="abs cert" style="left:703px;background:linear-gradient(135deg,#7a1024,#f7f4f1 50%,#7a1024)" role="img" aria-label="Certificate of achievement"></div>
<div class="abs cert" style="left:890px;background:linear-gradient(135deg,#3a2e6e,#f1ecf6 55%,#3a2e6e)" role="img" aria-label="Certificate"></div>
<div class="abs nav-arrow light" style="left:93px;top:3134px"><svg width="12" height="10" viewBox="0 0 12 10" fill="#111"><path d="M0 5 L5 1 V4 H12 V6 H5 V9 Z"/></svg></div>
<div class="abs nav-arrow dark" style="left:1076px;top:3134px"><svg width="12" height="10" viewBox="0 0 12 10" fill="#fff"><path d="M12 5 L7 1 V4 H0 V6 H7 V9 Z"/></svg></div>

<footer class="abs footer"></footer>
<div class="abs f-head" style="left:142px">QUICK LINKS</div>
<div class="abs f-line" style="left:142px"></div>
<span class="abs f-link" style="left:142px;top:3436px">Home</span>
<span class="abs f-link" style="left:142px;top:3472px">About Us</span>
<span class="abs f-link" style="left:142px;top:3508px">Services</span>
<span class="abs f-link" style="left:142px;top:3544px">Contact Us</span>

<div class="abs f-head" style="left:365px">CONTACT DETAILS</div>
<div class="abs f-line" style="left:365px"></div>
<svg class="abs" style="left:367px;top:3438px" width="11" height="14" viewBox="0 0 11 14" fill="#fff"><path d="M5.5 0 a5.5 5.5 0 0 1 5.5 5.5 C11 9 5.5 14 5.5 14 S0 9 0 5.5 A5.5 5.5 0 0 1 5.5 0z"/><circle cx="5.5" cy="5.5" r="2" fill="#14204f"/></svg>
<div class="abs f-link" style="left:389px;top:3436px;line-height:19px"><span class="f-sub">Address</span><br>48 Harbor Lane, Suite 210<br>Fairmont, VA 22190</div>
<svg class="abs" style="left:367px;top:3508px" width="12" height="12" viewBox="0 0 12 12" fill="#fff"><path d="M2 0 L4.5 0 L5.5 3 L4 4.5 C5 6.5 5.5 7 7.5 8 L9 6.5 L12 7.5 V10 C12 11 11 12 10 12 C4 12 0 8 0 2 C0 1 1 0 2 0z"/></svg>
<div class="abs f-link" style="left:389px;top:3506px;line-height:19px"><span class="f-sub">Phone</span><br>555 014 2288</div>
<svg class="abs" style="left:367px;top:3562px" width="13" height="10" viewBox="0 0 13 10" fill="none" stroke="#fff" stroke-width="1.4"><rect x=".7" y=".7" width="11.6" height="8.6"/><path d="M1 1 L6.5 5.5 L12 1"/></svg>
<div class="abs f-link" style="left:389px;top:3558px;line-height:19px"><span class="f-sub">Email</span><br>info@brisoluxgrp-example.com</div>

<div class="abs f-head" style="left:661px">FOLLOW US</div>
<div class="abs f-line" style="left:661px"></div>
<span class="abs f-link" style="left:663px;top:3438px"><i class="f-icon"></i>Linkora</span>
<span class="abs f-link" style="left:663px;top:3472px"><i class="f-icon"></i>Chirpwave</span>
<span class="abs f-link" style="left:663px;top:3508px"><i class="f-icon"></i>Snapgrid</span>
<span class="abs f-link" style="left:663px;top:3544px"><i class="f-icon"></i>Viewcast</span>

<div class="abs copyright">© 2024 Brisolux Federal Services. All Rights Reserved.</div>

</body>
</html>
```